Harborline Auto LLC

Car Dealer Customer Service
Address: 2874 Cresthaven Road, Shelbyville, TN 37162
web: www.harborlineautoxq.net
email: harborlineautoxq@mailnest.example
Phone: (931) 555-0148
Phone: (629) 555-0173

```html
<!DOCTYPE html>
<html lang="en">
<head>
<meta charset="utf-8">
<title>Harborline Auto – Business Card</title>
<link href="https://fonts.googleapis.com/css2?family=Poppins:wght@400;600;700&display=swap" rel="stylesheet">
<style>
  :root {
    --backdrop: #2b2b2b;
    --card: #f1f1f0;
    --blue: #1c6f9e;
    --blue-light: #2a8cc4;
    --gold: #e0a93b;
    --ink: #222;
  }
  * { box-sizing: border-box; margin: 0; padding: 0; }
  html, body { width: 1200px; height: 1138px; overflow: hidden; }
  body { background: var(--backdrop); font-family: "Poppins", sans-serif; position: relative; color: var(--ink); }

  .card {
    position: absolute;
    width: 620px;
    height: 375px;
    border-radius: 16px;
    background: var(--card);
    overflow: hidden;
  }
  .card--front { left: 274px; top: 186px; }
  .card--back  { left: 276px; top: 608px; }

  /* Front */
  .brand-mark { position: absolute; border-radius: 50%; background: var(--gold); }
  .card--front .brand-mark { width: 96px; height: 96px; left: 262px; top: 96px; }
  .brand-name {
    position: absolute;
    font-weight: 700;
    color: var(--blue);
    white-space: nowrap;
    letter-spacing: 0.5px;
  }
  .card--front .brand-name { left: 0; right: 0; text-align: center; top: 214px; font-size: 30px; }
  .front-web {
    position: absolute; left: 0; right: 0; top: 320px;
    display: flex; justify-content: center; align-items: center; gap: 22px;
    font-size: 15px;
  }
  .front-web .rule { width: 54px; height: 2px; background: var(--gold); }
  .front-bar { position: absolute; left: 0; right: 0; bottom: 0; height: 18px; display: flex; }
  .front-bar span { flex: 1; }
  .front-bar .blue { background: var(--blue); }
  .front-bar .gold { background: var(--gold); }

  /* Back */
  .wave { position: absolute; left: 0; top: 0; width: 620px; height: 375px; }
  .phones {
    position: absolute; right: 22px; top: 20px;
    color: #fff; font-weight: 700; font-size: 22px; line-height: 30px; letter-spacing: 1px;
  }
  .phones li { list-style: none; display: flex; align-items: center; justify-content: flex-end; gap: 10px; }
  .phones svg { width: 20px; height: 20px; }
  .card--back .brand-mark { width: 110px; height: 110px; left: 101px; top: 148px; }
  .card--back .brand-name { left: 36px; width: 240px; text-align: center; top: 308px; font-size: 23px; }

  .contact { position: absolute; right: 30px; text-align: right; }
  .person { top: 174px; }
  .person h1 { font-size: 24px; font-weight: 700; color: var(--blue); line-height: 32px; }
  .person p { font-size: 15.5px; line-height: 20px; }
  .address { top: 244px; font-size: 15.5px; line-height: 22px; }
  .links { top: 302px; font-size: 14px; line-height: 22px; list-style: none; }
  .links li { display: flex; align-items: center; justify-content: flex-end; gap: 10px; white-space: nowrap; }
  .links svg { width: 14px; height: 14px; flex: none; }
</style>
</head>
<body>

<section class="card card--front">
  <span class="brand-mark"></span>
  <div class="brand-name">HARBORLINE AUTO</div>
  <div class="front-web"><span class="rule"></span>www.harborlineautoxq.net<span class="rule"></span></div>
  <div class="front-bar"><span class="blue"></span><span class="gold"></span></div>
</section>

<section class="card card--back">
  <svg class="wave" viewBox="0 0 620 375" aria-hidden="true">
    <defs>
      <linearGradient id="headerBlue" x1="0" y1="0" x2="1" y2="0">
        <stop offset="0" stop-color="var(--blue-light)"/>
        <stop offset="1" stop-color="var(--blue)"/>
      </linearGradient>
    </defs>
    <path d="M0,0 H620 V138 C540,146 470,112 400,78 C300,30 160,14 0,30 Z" fill="url(#headerBlue)"/>
    <path d="M0,50 C140,20 280,30 380,80 C470,126 540,140 620,132 V146 C540,156 460,136 370,92 C270,44 140,36 0,64 Z" fill="var(--gold)"/>
    <path d="M10,68 C130,46 240,50 330,70 C240,58 130,58 10,72 Z" fill="var(--gold)"/>
  </svg>

  <ul class="phones">
    <li>931-555-0148
      <svg viewBox="0 0 24 24" fill="#fff"><path d="M6.6 10.8a15 15 0 006.6 6.6l2.2-2.2a1 1 0 011-.25 11.4 11.4 0 003.6.57 1 1 0 011 1V20a1 1 0 01-1 1A17 17 0 013 4a1 1 0 011-1h3.5a1 1 0 011 1c0 1.25.2 2.45.57 3.6a1 1 0 01-.25 1z"/></svg>
    </li>
    <li>629-555-0173
      <svg viewBox="0 0 24 24" fill="#fff"><path d="M6.6 10.8a15 15 0 006.6 6.6l2.2-2.2a1 1 0 011-.25 11.4 11.4 0 003.6.57 1 1 0 011 1V20a1 1 0 01-1 1A17 17 0 013 4a1 1 0 011-1h3.5a1 1 0 011 1c0 1.25.2 2.45.57 3.6a1 1 0 01-.25 1z"/></svg>
    </li>
  </ul>

  <span class="brand-mark"></span>
  <div class="brand-name">HARBORLINE AUTO</div>

  <div class="contact person">
    <h1>Darren Whitlow</h1>
    <p>Managing Director</p>
  </div>
  <p class="contact address">2874 Cresthaven Road,<br>Shelbyville, TN 37162</p>
  <ul class="contact links">
    <li>www.harborlineautoxq.net
      <svg viewBox="0 0 24 24" fill="none" stroke="var(--gold)" stroke-width="2.4"><circle cx="12" cy="12" r="10"/><path d="M2 12h20M12 2c3 3 3 17 0 20M12 2c-3 3-3 17 0 20"/></svg>
    </li>
    <li>harborlineautoxq@mailnest.example
      <svg viewBox="0 0 24 24" fill="var(--gold)"><path d="M2 5h20v14H2z"/><path d="M2 5l10 8 10-8" fill="none" stroke="#fff" stroke-width="2"/></svg>
    </li>
  </ul>
</section>

</body>
</html>
```